KRL Stationery Design Project

Dear Designers,
We need a new stationery design for company to match our new logo.
Designers should provide a design for the following:
1. Business Card: 3.5x2 Inches.
2. Letterhead: A4 size.
3. Envelops: 25x35.5 Cm.
You can keep the Arabic name at the bottom of the logo Or you can use the separate attached Arabic Name.
Please refer to the attached logo guide for design information.
Sample Business Card information:
Name: Tarek Sowan
Position: Operation Manager
Tel: +966 920007164 Ex. 500
Fax: +966 (3)8842617
Mob: +966 (5)00263817
email: tarek@krl-example.com.sa
URL: www.krl-example.com.sa
Address:
Nakheel Heights, Suite 718
Zayed bin Omar Str.
Khobar, 31847
Saudi Arabia
Updates
Dear All,
Please note, we had uploaded our logo along with Arabic writing in Adobe illustrator format (.ai).
Regards,
Karim
Dear All,
A sample data for the business card had been added as per your request.
Regards,
Karim

```html
<!DOCTYPE html>
<html lang="en">
<head>
<meta charset="utf-8">
<title>KRL Letterhead</title>
<link rel="stylesheet" href="https://fonts.googleapis.com/css2?family=Saira+Condensed:wght@400;700&display=swap">
<style>
  :root {
    --navy: #173356;
    --ink: #3a3a3a;
    --frame: #c4c4c4;
    --paper: #ffffff;
  }
  * { margin: 0; padding: 0; box-sizing: border-box; }
  html, body {
    width: 863px;
    height: 1200px;
    overflow: hidden;
    background: var(--paper);
  }
  .letterhead {
    position: relative;
    width: 863px;
    height: 1200px;
    background: var(--paper);
    font-family: "Saira Condensed", "Arial Narrow", sans-serif;
  }
  .page-edge {
    position: absolute;
    left: 19px;
    top: 19px;
    width: 825px;
    height: 1162px;
    border: 1px solid var(--frame);
  }
  .brand {
    position: absolute;
    right: 50px;
    top: 50px;
    display: flex;
    align-items: center;
    gap: 14px;
  }
  .brand-mark {
    width: 34px;
    height: 34px;
    background: var(--navy);
  }
  .brand-name {
    font-size: 70px;
    font-weight: 700;
    line-height: 1;
    letter-spacing: 2px;
    color: var(--navy);
  }
  .footer {
    position: absolute;
    left: 41px;
    right: 41px;
    top: 1110px;
    border-top: 3px solid var(--navy);
    padding-top: 10px;
    text-align: center;
    color: var(--ink);
    font-size: 15px;
    line-height: 24px;
    white-space: nowrap;
    overflow: hidden;
  }
</style>
</head>
<body>
  <main class="letterhead">
    <div class="page-edge"></div>

    <header class="brand">
      <span class="brand-mark"></span>
      <span class="brand-name">KRL</span>
    </header>

    <footer class="footer">
      <p class="footer-address">Nakheel Heights, Suite 718, Zayed bin Omar Str., Khobar, 31847, Saudi Arabia</p>
      <p class="footer-contacts">Tel: +966 920007164 Ex. 500 | Fax: +966 (3)8842617 | email: tarek@krl-example.com.sa | URL: www.krl-example.com.sa</p>
    </footer>
  </main>
</body>
</html>
```